Etikett für Likörflasche - Tinderbox
Zielgruppe
Wir sind eine kleine Tinderbox / Likörmanufaktur. Unser Obst für die Brände und Liköre stammt aus eigenem Anbau bzw. von umliegenden regionalen Bauern. Hier setzen wir auf sehr gute Qualität und verwenden keine Zusatzstoffe, Geschmacksverstärker, Farbstoffe etc. Im ersten Schritt werden wir nur 3-4 verschiedene Liköre anbieten.
Wir möchten unsere Liköre zukünftig auf Veranstaltungen / Events und Märkten verkaufen. Hierfür suchen wir ein pfiffiges und ansprechendes Etikettendesign.
Das Wort 'Tinderbox' soll die Leute auf den Events zu uns führen. Das wird auch mit großen Fahnen am Verkaufsstand beworben. Da wir auch ein paar amerikanische Foodtrucks haben soll auch das Etikett ein bisschen amerikanisch gehalten werden.
Zielgruppe: 28 bis 55 Jahre (Männer & Frauen)
Verkaufspreis pro 0,5 Liter Flasche ca. 24,50 Euro
Aufgabenstellung
Es soll ein Etikett auf die Flasche (nur vorne nicht auf die Rückseite).
Etikettengröße: ca. 7,0 x 8,5cm (für die 0,5l Flasche)
Angaben die sich auf dem Etikett ändern:
- Inhalt entweder 0,35l oder 0,5l Flasche
- Bezeichnung vom Inhalt und 'Kurzbeschreibung'
- Alkoholgehalt
Ich habe in PowerPoint schon mal ein Etikett zusammen gestellt, auf dem die Angaben alle mit enthalten sind. Hier fehlt mir allerdings der Pfiff und das Professionelle. Auch die Darstellung der Eigenschaften wie 'Echte Früchte', 'Handcrafted' etc. gefällt mir so auch nicht. Vielleicht wäre auch noch ein cooler Spruch darauf gut.
In die Anlage habe ich meine kreierte PowerPoint Folie gepackt (auf der 2. Folie findet ihr die geplante Flasche in die abgefüllt wird). Die zweite Datei ist ein Design was meinen Vorstellungen schon gut nahe kommt aus dem Internet (hier gefallen mir die Linien, kleine Gimmicks etc. da passiert einfach was auf dem Etikett). Von der Art her würde mir dieser Style gut gefallen. Es soll nur nicht zu überladen und kitschig werden.
Likörsorten die es geben wird: Wir werden uns erstmal auf 3-4 Sorten beschränken.

```html
<!DOCTYPE html>
<html lang="de">
<head>
<meta charset="utf-8">
<title>Hollis' Tinderbox – Etikett Dusty and Berry</title>
<link rel="stylesheet" href="https://fonts.googleapis.com/css2?family=Oswald:wght@500;600&family=Questrial&family=Permanent+Marker&family=Amatic+SC:wght@400;700&display=block">
<style>
  :root {
    --stage-top: #416586;
    --stage-bottom: #263850;
    --paper-light: #efe0b8;
    --paper-mid: #e3cc9a;
    --paper-edge: #c9ab74;
    --paper-stain: rgba(170, 130, 70, 0.18);
    --ink-navy: #2b2b5c;
    --ink-navy-soft: rgba(43, 43, 92, 0.75);
    --ink-red: #c9252b;
    --caption: #ffffff;
  }
  * { margin: 0; padding: 0; box-sizing: border-box; }
  html, body { width: 1200px; height: 2400px; overflow: hidden; }
  body {
    background: linear-gradient(180deg, var(--stage-top) 0%, var(--stage-bottom) 100%);
    font-family: "Oswald", sans-serif;
    position: relative;
  }
  .label-caption {
    position: absolute; left: 150px; top: 560px;
    font-family: "Questrial", sans-serif; font-size: 56px; font-weight: 400;
    color: var(--caption); letter-spacing: 1px;
  }
  .label {
    position: absolute; left: 150px; top: 680px;
    width: 900px; height: 1093px; overflow: hidden;
    background:
      radial-gradient(ellipse 30% 22% at 30% 22%, var(--paper-stain), transparent 70%),
      radial-gradient(ellipse 26% 18% at 72% 62%, var(--paper-stain), transparent 70%),
      radial-gradient(ellipse at 45% 40%, var(--paper-light) 0%, var(--paper-mid) 62%, var(--paper-edge) 100%);
    color: var(--ink-navy);
  }
  .label > * { position: absolute; }
  .label-frame { left: 0; top: 0; width: 900px; height: 1093px; }
  .corner-star { width: 72px; height: 72px; top: 40px; }
  .corner-star.left { left: 30px; }
  .corner-star.right { left: 787px; }

  .famous {
    left: 114px; top: 140px; font-size: 50px; font-weight: 500; line-height: 1;
    transform: rotate(-8deg); transform-origin: left bottom; white-space: nowrap;
  }
  .shooting-star {
    left: 492px; top: 132px; width: 296px; height: 96px;
    background: linear-gradient(165deg, rgba(43,43,92,0) 10%, rgba(43,43,92,.35) 55%, rgba(43,43,92,.7) 100%);
    border-radius: 80% 20% 70% 30% / 60% 40% 60% 40%;
  }

  .brand {
    left: 130px; top: 222px; width: 660px; text-align: center;
    font-weight: 600; color: var(--ink-navy); line-height: 1;
  }
  .brand-owner { display: block; font-size: 54px; letter-spacing: 3px; }
  .brand-name { display: block; font-size: 118px; letter-spacing: 5px; margin-top: 2px; }

  .spec { top: 450px; font-size: 33px; font-weight: 500; line-height: 1; transform: translateX(-50%); white-space: nowrap; }
  .spec.volume { left: 269px; }
  .spec.abv { left: 448px; }
  .spec.proof { left: 617px; }

  .rule { left: 148px; width: 624px; height: 3px; background: var(--ink-navy); }
  .rule.upper { top: 497px; }
  .rule.lower { top: 607px; }
  .product {
    left: 148px; top: 504px; width: 624px; text-align: center;
    font-size: 84px; font-weight: 600; line-height: 1.15; letter-spacing: -1px; white-space: nowrap;
  }
  .seasoning {
    left: 148px; top: 616px; width: 624px; text-align: center;
    font-family: "Permanent Marker", cursive; font-size: 30px; line-height: 1.2; color: var(--ink-red);
  }
  .description {
    left: 148px; top: 658px; width: 624px; text-align: center;
    font-size: 31px; font-weight: 500; line-height: 1.55;
  }
  .flourish {
    left: 323px; top: 770px; width: 246px; height: 46px;
    background: linear-gradient(90deg, var(--ink-navy-soft), rgba(43,43,92,.3));
    border-radius: 50%;
  }

  .claim { font-family: "Permanent Marker", cursive; color: var(--ink-red); font-size: 25px; line-height: 1; white-space: nowrap; }
  .claim.handcrafted { left: 170px; top: 848px; transform: rotate(-15deg); transform-origin: left top; }
  .claim.handcrafted span { display: block; padding-left: 34px; }
  .claim.additives { left: 566px; top: 826px; transform: rotate(15deg); transform-origin: left top; }

  .address {
    left: 290px; top: 878px; width: 320px; text-align: center;
    font-size: 30px; font-weight: 500; line-height: 1.22; font-style: normal;
  }
  .web {
    left: 230px; top: 1010px; width: 440px; text-align: center;
    font-size: 28px; font-weight: 500; line-height: 1.2;
  }

  .slogan { font-family: "Amatic SC", cursive; font-weight: 400; color: var(--ink-red); line-height: .92; }
  .slogan.real-taste { left: 26px; top: 930px; font-size: 66px; }
  .slogan.one-and-only { left: 752px; top: 900px; font-size: 58px; transform: rotate(-4deg); }
  .slogan.one-and-only span { display: block; }
  .slogan.one-and-only .l1 { padding-left: 34px; }

  .font-list {
    position: absolute; left: 150px; top: 1850px;
    font-family: "Questrial", sans-serif; font-size: 29px; line-height: 1.3;
    color: var(--caption); list-style: none;
  }
  .font-list .heading { font-weight: 700; }
</style>
</head>
<body>
  <h1 class="label-caption">Label 7 x 8,5 cm</h1>

  <section class="label" aria-label="Flaschenetikett Dusty and Berry">
    <svg class="label-frame" viewBox="0 0 900 1093" aria-hidden="true">
      <path d="M119 88 L781 88 A40 40 0 0 0 821 128 L740 962 A40 40 0 0 0 700 1002 L200 1002 A40 40 0 0 0 160 962 L79 128 A40 40 0 0 0 119 88 Z"
            fill="none" stroke="var(--ink-navy)" stroke-width="4"/>
    </svg>

    <svg class="corner-star left" viewBox="0 0 100 100" aria-hidden="true">
      <polygon points="50,6 61,38 95,38 67,58 78,92 50,71 22,92 33,58 5,38 39,38" fill="none" stroke="var(--ink-red)" stroke-width="6" stroke-linejoin="round"/>
    </svg>
    <svg class="corner-star right" viewBox="0 0 100 100" aria-hidden="true">
      <polygon points="50,6 61,38 95,38 67,58 78,92 50,71 22,92 33,58 5,38 39,38" fill="none" stroke="var(--ink-red)" stroke-width="6" stroke-linejoin="round"/>
    </svg>

    <p class="famous">THE FAMOUS</p>
    <div class="shooting-star" role="img" aria-label="Gezeichnete Sternschnuppe als Schmuckelement"></div>

    <h2 class="brand">
      <span class="brand-owner">HOLLIS'</span>
      <span class="brand-name">TINDERBOX</span>
    </h2>

    <p class="spec volume">500 ML</p>
    <p class="spec abv">22 % VOL.</p>
    <p class="spec proof">44 PROOF</p>

    <div class="rule upper"></div>
    <h3 class="product">DUSTY AND BERRY</h3>
    <div class="rule lower"></div>

    <p class="seasoning">Seasoned Fruits</p>
    <p class="description">WILDE BEEREN TREFFEN AUF VIELSCHICHTIGE<br>NOTEN VON WHISKEY UND KARAMELL</p>

    <div class="flourish" role="img" aria-label="Geschwungene Zierlinie"></div>

    <p class="claim handcrafted">Complete<span>Handcrafted</span></p>
    <p class="claim additives">No Additives</p>

    <address class="address">HOLLIS' TINDERBOX<br>AM LINDENHANG 12<br>91299 FALKENRIED</address>
    <p class="web">WWW.HOLLIS-TINDERBOX.DE</p>

    <p class="slogan real-taste">REAL<br>TASTE</p>
    <p class="slogan one-and-only"><span class="l1">THE</span><span>ONE &amp;</span><span>ONLY</span></p>
  </section>

  <ul class="font-list">
    <li class="heading">Verwendete Schriften:</li>
    <li>Airfield Sans Regular</li>
    <li>Scribbla Doodle Reglar</li>
    <li>The Drifter</li>
  </ul>
</body>
</html>
```